Wordpress Design Project (Brindlow)

We need a wordpress design for an established auction and real estate company based in New Jersey. The winning design will incorporate a professional color scheme and company logo in a clean layout.

Industry/Entity Type

Real Estate

Requirements
Must have
• - We will require winning designer to provide a layered PSD (Adobe photoshop) concept file, along with any non-standard font files used.

Logo attached. Will hopefully post better logo shortly. Please use site design colors of your choice as the logo is black & white. A site client mentions liking is http://www.qelmarbidding.example/. Homepage content will be an auction list as seen at http://www.gavelroundup.example/?page=5

Horizontal Navigation menu with these pages:
Home - Auction Calendar - Appraisals - Services - Company Profile - News & Events - Testimonials - Contact Us

A slideshow element on the home page using one of the placeholder images provided (or stock if higher resolution image is necessary).

Sidebar widgets to be included are: Email sign-up form - Featured Auctions - Testimonial widget - 'Our Videos' widget; Social media icons somewhere in layout (facebook, twitter, RSS, and Youtube)

Homepage content is text:
BRINDLOW MANAGEMENT COMPANY was founded 90 years ago in 1921 by Harold Brindlow, which makes us one of the oldest commercial and industrial auction and appraisal companies in America.

We have conducted thousands of auctions, assisting a wide range of companies both large and small achieve maximum value for their capital assets.
Nice to have
• - Site will have drop down menus, nice to have a sample look for them on one of the primary menu items.

```html
<!DOCTYPE html>
<html lang="en">
<head>
<meta charset="utf-8">
<title>Brindlow Auctioneers &amp; Appraisers</title>
<link href="https://fonts.googleapis.com/css2?family=Questrial&display=swap" rel="stylesheet">
<style>
:root{
  --black:#000;
  --teal:#0f7e87;
  --teal-dark:#0b6a72;
  --ink:#222;
  --muted:#666;
  --page:#f7f7f7;
  --line:#e2e2e2;
  --bar-top:#555;
  --bar-bottom:#1e1e1e;
}
*{margin:0;padding:0;box-sizing:border-box}
html,body{width:674px;height:1200px;overflow:hidden}
body{position:relative;background:var(--page);font-family:"Questrial",sans-serif;color:var(--ink)}
.abs{position:absolute}
.header-band{left:0;top:0;width:674px;height:176px;background:var(--black)}
.brand{left:72px;top:29px;width:110px;height:33px;background:#fff;border:1px solid #999;display:flex;align-items:center;justify-content:center;gap:5px;font-size:12px;letter-spacing:.5px;color:#111}
.brand i{width:9px;height:9px;background:#111;display:block}
.social{top:20px;display:flex;gap:4px;left:520px}
.social span{width:18px;height:18px;border-radius:50%;display:block}
.search{left:462px;top:49px;width:111px;height:13px;background:#fff;border:1px solid #ccc;font-size:6px;color:#999;padding:2px 6px}
.go{left:578px;top:49px;width:24px;height:13px;background:var(--teal);color:#fff;font-size:7px;text-align:center;line-height:13px}
.nav{left:70px;top:70px;width:533px;height:29px;background:linear-gradient(#f2f2f2,#d3d3d3);display:flex;justify-content:space-around;align-items:center;font-size:8.4px;color:#222;padding:0 6px}
.slider{left:70px;top:110px;width:533px;height:172px;background:linear-gradient(180deg,#8fb7d9 0%,#b9c9d6 30%,#b3262d 55%,#8d1c22 80%,#5a5a5a 100%)}
.dots{left:86px;top:259px;display:flex;gap:4px}
.dots span{width:7px;height:7px;border-radius:50%;background:#fff}
.dots span.on{background:var(--teal)}
h1,h2{font-weight:400}
.welcome{left:70px;top:302px;font-size:14.5px}
.intro{left:70px;top:326px;width:354px;font-size:7.6px;line-height:13.6px;color:var(--muted);text-align:justify}
.live{left:70px;top:388px;font-size:13.5px}
.card{left:70px;width:354px;height:154px;background:#fff;border:1px solid var(--line)}
.card .photo{left:13px;top:10px;width:118px;height:96px;background:linear-gradient(#9cc0e0,#c9b79a 55%,#5f8a3e)}
.card h3{left:145px;top:9px;font-size:10.2px;font-weight:400}
.card p{left:146px;top:26px;width:200px;font-size:6.2px;line-height:12px;color:#333}
.card .tag{left:144px;top:56px;width:191px;height:51px;background:var(--teal);padding:6px 10px;color:#fff}
.tag b{display:block;font-weight:400;font-size:8px;margin-bottom:3px}
.tag span{display:block;font-size:6px;line-height:12px;color:#9fd3d7}
.card .bar{left:-1px;top:116px;width:354px;height:38px;background:linear-gradient(var(--bar-top),var(--bar-bottom));color:#ddd;font-size:8px}
.bar .lbl{top:15px;display:flex;align-items:center;gap:8px}
.bar .more{left:291px;top:13px;width:55px;height:13px;background:var(--teal);color:#fff;font-size:6px;text-align:center;line-height:13px;border-bottom:1px solid #034}
.pager{left:171px;top:1097px;display:flex;gap:5px}
.pager span{height:16px;min-width:18px;padding:0 5px;border:1px solid #ccc;background:#fff;font-size:7px;line-height:14px;text-align:center}
.news{left:452px;top:300px;width:151px;height:171px;background:linear-gradient(#2a2a2a,#050505);color:#fff;padding:10px 12px}
.news h4{font-weight:400;font-size:8.4px;display:flex;align-items:center;gap:6px;margin-top:1px}
.news p{font-size:6.2px;line-height:11px;color:#aaa;margin-top:15px;text-align:justify}
.field{height:17px;background:#444;border:1px solid #555;font-size:6.2px;color:#bbb;padding:4px 6px;margin-top:8px}
.news .btn{width:57px;height:16px;background:var(--teal);font-size:7.6px;text-align:center;line-height:16px;margin:13px auto 0}
.side-h{left:452px;width:152px;font-size:10px;display:flex;justify-content:space-between;align-items:center}
.arrows{display:flex;gap:2px}
.arrows span{width:12px;height:12px;border-radius:50%;background:#333;color:#fff;font-size:7px;text-align:center;line-height:12px}
.feat{left:452px;top:517px;width:151px;height:201px;background:var(--teal);color:#fff;padding:12px 11px}
.feat .photo{width:130px;height:95px;background:linear-gradient(#a9c8e6,#7a5a48 50%,#4f7d36)}
.feat h5{font-weight:400;font-size:10px;margin-top:6px}
.feat p{font-size:6.2px;line-height:12.4px;margin-top:4px}
.testi{left:452px;top:756px;width:151px;height:178px;background:#fff;border:1px solid var(--line);border-bottom:3px solid #ddd;padding:10px 10px}
.testi p{font-size:7.4px;line-height:13.4px;color:#555;text-align:justify}
.testi .name{color:var(--teal);font-size:10.2px;margin-top:4px;padding-left:3px}
.testi .role{font-size:7.4px;color:#333;padding-left:3px;margin-top:2px}
.video{left:452px;top:986px;width:151px;height:100px;background:linear-gradient(135deg,#d9c9a4,#9fbce0 55%,#2a6fc4)}
.play{left:57px;top:39px;width:36px;height:20px;background:rgba(0,0,0,.65);border-radius:3px}
.vbar{left:0;top:90px;width:151px;height:10px;background:rgba(0,0,0,.7)}
.footer{left:0;top:1148px;width:674px;height:52px;background:var(--black);color:#fff;text-align:center}
.footer .links{font-size:8.2px;margin-top:14px;word-spacing:1px}
.footer .copy{font-size:8px;margin-top:10px}
</style>
</head>
<body>
<div class="abs header-band"></div>
<div class="abs brand"><i></i>BRINDLOW</div>
<div class="abs social" aria-label="Social links">
  <span style="background:#3b5998"></span><span style="background:#2aa9e0"></span><span style="background:#f08a24"></span><span style="background:#d6312b"></span>
</div>
<div class="abs search">Search...</div>
<div class="abs go">Go</div>
<nav class="abs nav"><span>Home</span><span>Auction Calendar</span><span>Appraisals</span><span>Services</span><span>Company Profile</span><span>News &amp; Events</span><span>Testimonials</span><span>Contact Us</span></nav>
<div class="abs slider" role="img" aria-label="Row of red semi trucks parked in a lot"></div>
<div class="abs dots"><span></span><span></span><span></span><span class="on"></span></div>

<h1 class="abs welcome">Welcome to Brindlow</h1>
<p class="abs intro">BRINDLOW MANAGEMENT COMPANY was founded 90 years ago in 1921 by Harold Brindlow, which makes us one of the oldest commercial and industrial auction and appraisal companies in America.We have conducted thousands of auctions, assisting a wide range of companies both large and small achieve maximum value for their capital assets.</p>
<h2 class="abs live">Live Auctions</h2>

<div class="abs card" style="top:422px">
  <div class="abs photo" role="img" aria-label="Large lodge-style residence"></div>
  <h3 class="abs">Real Estate Aution 2013</h3>
  <p class="abs">Lorem ipsum dolor sit amet, consectetur adipisicing elit, sed do eiusmod tempor incididunt .</p>
  <div class="abs tag"><b>Live On-Site Auction</b><span>Begins: Saturday, August 10, 2013 at 10:00 AM EDT</span><span>Location: 4120 Route 9, Oak Ridge, NJ 07438</span></div>
  <div class="abs bar"><div class="abs lbl" style="left:47px">&#9634; Details</div><div class="abs lbl" style="left:124px">&#9635; Pictures</div><div class="abs more">Read More</div></div>
</div>
<div class="abs card" style="top:590px">
  <div class="abs photo" role="img" aria-label="Cream townhouses on a street"></div>
  <h3 class="abs">Real Estate Aution 2013</h3>
  <p class="abs">Lorem ipsum dolor sit amet, consectetur adipisicing elit, sed do eiusmod tempor incididunt .</p>
  <div class="abs tag"><b>Live On-Site Auction</b><span>Begins: Saturday, August 10, 2013 at 10:00 AM EDT</span><span>Location: 4120 Route 9, Oak Ridge, NJ 07438</span></div>
  <div class="abs bar"><div class="abs lbl" style="left:47px">&#9634; Details</div><div class="abs lbl" style="left:124px">&#9635; Pictures</div><div class="abs more">Read More</div></div>
</div>
<div class="abs card" style="top:761px">
  <div class="abs photo" role="img" aria-label="Two-storey family house with lawn"></div>
  <h3 class="abs">Real Estate Aution 2013</h3>
  <p class="abs">Lorem ipsum dolor sit amet, consectetur adipisicing elit, sed do eiusmod tempor incididunt .</p>
  <div class="abs tag"><b>Live On-Site Auction</b><span>Begins: Saturday, August 10, 2013 at 10:00 AM EDT</span><span>Location: 4120 Route 9, Oak Ridge, NJ 07438</span></div>
  <div class="abs bar"><div class="abs lbl" style="left:47px">&#9634; Details</div><div class="abs lbl" style="left:124px">&#9635; Pictures</div><div class="abs more">Read More</div></div>
</div>
<div class="abs card" style="top:933px">
  <div class="abs photo" role="img" aria-label="Red for-sale sign in front of a house" style="background:linear-gradient(90deg,#c8202a 45%,#b9c4cf 45%,#7fa35a)"></div>
  <h3 class="abs">Real Estate Aution 2013</h3>
  <p class="abs">Lorem ipsum dolor sit amet, consectetur adipisicing elit, sed do eiusmod tempor incididunt .</p>
  <div class="abs tag"><b>Live On-Site Auction</b><span>Begins: Saturday, August 10, 2013 at 10:00 AM EDT</span><span>Location: 4120 Route 9, Oak Ridge, NJ 07438</span></div>
  <div class="abs bar"><div class="abs lbl" style="left:47px">&#9634; Details</div><div class="abs lbl" style="left:124px">&#9635; Pictures</div><div class="abs more">Read More</div></div>
</div>

<div class="abs pager"><span>Prev</span><span>1</span><span>2</span><span>3</span><span>4</span><span>5</span><span>6</span><span></span><span>22</span><span>Next</span></div>

<aside class="abs news">
  <h4><svg width="16" height="11" viewBox="0 0 16 11"><rect x=".5" y=".5" width="15" height="10" fill="none" stroke="#fff"/><path d="M.5 .5 8 6l7.5-5.5" fill="none" stroke="#fff"/></svg>Sign Up For Newsletter</h4>
  <p>Lorem dolor sit amet, consectetur adipisicing elit, sed do eiusmod tempor</p>
  <div class="field">Name</div>
  <div class="field">E-Mail Address</div>
  <div class="btn">Sign Up</div>
</aside>

<div class="abs side-h" style="top:491px">Featured Auctions<div class="arrows"><span>&#8249;</span><span>&#8250;</span></div></div>
<div class="abs feat">
  <div class="photo" role="img" aria-label="Brick house with green lawn"></div>
  <h5>Live Auction Today</h5>
  <p><b>Begins:</b> Saturday, August 10, 2013 at 9:00 AM CDT<br><b>Location:</b> 2250 MILLBROOK RD, HOPEWELL, NJ 08525</p>
</div>

<div class="abs side-h" style="top:730px">Testimonials<div class="arrows"><span>&#8249;</span><span>&#8250;</span></div></div>
<div class="abs testi">
  <p>&ldquo; Sed ut perspiciatis unde omnis iste natus error sit voluptatem accusantium eaque ipsa quae ab illo inventore veritatis et quasi architecto beatae vitae dicta sunt explicabo. Nemo enim ipsam voluptatem quia voluptas sit aspernatur aut odit aut fugit, sed quia consequuntur &rdquo;</p>
  <div class="name">Dana Whitfield</div>
  <div class="role">Auction Director New york</div>
</div>

<div class="abs side-h" style="top:954px">Featured Video<div class="arrows"><span>&#8249;</span><span>&#8250;</span></div></div>
<div class="abs video" role="img" aria-label="Video still of a hand holding house keys">
  <div class="abs play"><svg width="36" height="20" viewBox="0 0 36 20"><path d="M15 6l7 4-7 4z" fill="#fff"/></svg></div>
  <div class="abs vbar"></div>
</div>

<footer class="abs footer">
  <div class="links">Home &nbsp;|&nbsp; Auction Calendar &nbsp;|&nbsp; Appraisals &nbsp;|&nbsp; Services &nbsp;|&nbsp; Company Profile &nbsp;|&nbsp; News &amp; Events &nbsp;|&nbsp; Testimonials &nbsp;|&nbsp; Contact Us</div>
  <div class="copy">Copyright &copy;2013 Company Name &nbsp; - All rights reserved</div>
</footer>
</body>
</html>
```